Business Card Design

We require a business card design for a law firm, our signature colours are maroon and cream. Our slogan is "From our family to yours", we would like the cards to be professional however feminine at the same time.

Industry/Entity Type

Business

Contact Information for Business Card

Helena Drace & Associates Lawyers & Conveyancers, Helena Drace LL.B. Principal Solicitor, 17 Kellow Street, Marrick NSW 2299

Logo styles of interest
Emblem Logo
Abstract Logo
Wordmark Logo

```html
<!DOCTYPE html>
<html lang="en">
<head>
<meta charset="utf-8">
<title>Helena Drace &amp; Associates – Business Card</title>
<link rel="stylesheet" href="https://fonts.googleapis.com/css2?family=Tinos&family=Dancing+Script:wght@500&display=swap">
<style>
  :root {
    --cream: #fdf9d8;
    --maroon: #7d1a14;
    --maroon-soft: #e9d3bd;
  }
  html, body {
    margin: 0;
    padding: 0;
    width: 1200px;
    height: 726px;
    overflow: hidden;
    background: var(--cream);
  }
  .card {
    position: relative;
    width: 1200px;
    height: 726px;
    background: var(--cream);
    color: var(--maroon);
    font-family: "Tinos", "Times New Roman", serif;
  }
  .emblem {
    position: absolute;
    left: 458px;
    top: 50px;
    width: 323px;
    height: 316px;
  }
  .firm-name {
    position: absolute;
    left: 0;
    width: 1262px;
    top: 380px;
    margin: 0;
    text-align: center;
    font-weight: 400;
    font-size: 44px;
    line-height: 56px;
  }
  .slogan {
    position: absolute;
    left: 0;
    width: 1262px;
    top: 506px;
    margin: 0;
    text-align: center;
    font-family: "Dancing Script", cursive;
    font-weight: 500;
    font-size: 23px;
  }
  .contact {
    position: absolute;
    top: 561px;
    margin: 0;
    font-size: 33px;
    line-height: 44px;
  }
  .contact--person { left: 64px; }
  .contact--address { left: 839px; }
</style>
</head>
<body>
  <main class="card">
    <svg class="emblem" role="img" aria-label="Scales of justice emblem with flourishes" viewBox="0 0 323 316">
      <defs>
        <radialGradient id="emblemTone" cx="50%" cy="50%" r="60%">
          <stop offset="0" stop-color="#c79a8a"/>
          <stop offset="1" stop-color="#efe2c4"/>
        </radialGradient>
      </defs>
      <rect width="323" height="316" fill="url(#emblemTone)"/>
    </svg>

    <h1 class="firm-name">Helena Drace &amp; Associates<br>Lawyers &amp; Conveyancers</h1>
    <p class="slogan">From our family to yours</p>

    <p class="contact contact--person">Helena Drace LL.B.<br>Principal Solicitor</p>
    <p class="contact contact--address">17 Kellow Street<br>Marrick NSW 2299</p>
  </main>
</body>
</html>
```